Elegant Business Card for Technology Company

Client is a supplier of innovative industrial communications and automation equipment since 2002. This contest is to gather fresh ideas for a redesign of the existing business card. Client is looking for design that best communicates tagline "Industrial Networking and Computing Specialist".

Design submissions should look modern, clean, elegant and professional. It should not be cluttered. Use white as the primary colour. Orange and black as secondary colour. Refer to jpeg File 1 on the current design.

Fonts used by Client used include Arial Regular, Arial Black, Roboto Regular, Roboto Black and Lato.

The winning design will be sent for offset printing using super white 250gsm artcard paper (open for suggestions).

Target Market(s)

System Engineers, Project Managers, Purchasing Managers from companies providing engineering services for Smart Cities.

Industry/Entity Type

Information Technology

Contact Information for Business Card

Refer to PDF File 3 for Business Card Details. Priority of short contact information would be as follows Name > Job Title > Email > Mobile > Web > Tel > Fax > Business Address >UEN (UEN represents company registration number)

Font styles to use
Sans Serif

Colors
ffffff
f37122
000000
5c5c5c

Requirements
Must have
• Refer to AI File 2 (Company Logo) & PDF File 3 (Information on Namecard)
Should not have
• No QR codes
• No Social Media Icons
• Do not create full Black or Orange colour background

```html
<!DOCTYPE html>
<html lang="en">
<head>
<meta charset="utf-8">
<title>KVR Business Card</title>
<link href="https://fonts.googleapis.com/css2?family=Roboto:wght@400;500;700&display=swap" rel="stylesheet">
<style>
  :root {
    --white: #ffffff;
    --orange: #f37122;
    --orange-deep: #c45816;
    --black: #000000;
    --grey: #5c5c5c;
    --stage: #e9e6e1;
  }
  * { margin: 0; padding: 0; box-sizing: border-box; }
  html, body { width: 1200px; height: 950px; overflow: hidden; }
  body {
    background: var(--stage);
    font-family: "Roboto", Arial, sans-serif;
    display: flex;
    flex-direction: column;
    align-items: center;
    justify-content: center;
    gap: 50px;
  }
  .card {
    width: 700px;
    height: 400px;
    position: relative;
    overflow: hidden;
    background: var(--white);
    box-shadow: 0 6px 18px rgba(0,0,0,0.18);
  }

  /* Back side: white base with orange accent bands */
  .card-back {
    display: flex;
    flex-direction: column;
    align-items: center;
    justify-content: center;
    padding: 0 40px;
  }
  .back-band {
    position: absolute; left: 0; right: 0;
    background: linear-gradient(120deg, var(--orange) 0%, var(--orange-deep) 100%);
  }
  .back-band-top { top: 0; height: 14px; }
  .back-band-bottom { bottom: 0; height: 34px; }
  .back-mark {
    display: flex;
    align-items: center;
    gap: 18px;
    margin-bottom: 34px;
  }
  .back-mark .mark-dot {
    width: 96px; height: 96px; border-radius: 50%;
    background: var(--orange);
  }
  .back-mark .mark-name {
    font-size: 60px; font-weight: 700; color: var(--black); letter-spacing: 2px;
  }
  .tagline {
    text-align: center; font-size: 18px; line-height: 1.5;
    letter-spacing: 0.6px; color: var(--grey);
    margin-bottom: 20px;
  }
  .tagline .lead { font-size: 21px; font-weight: 500; color: var(--orange); }

  /* Front side */
  .brand {
    position: absolute; left: 44px; top: 40px;
    display: flex; align-items: center; gap: 16px;
  }
  .brand .brand-dot {
    width: 78px; height: 78px; border-radius: 50%; background: var(--orange);
  }
  .brand .brand-name {
    font-size: 62px; font-weight: 700; color: var(--black); letter-spacing: 1px;
  }
  .divider {
    position: absolute; left: 44px; right: 44px; top: 168px;
    height: 2px; background: var(--orange);
  }
  .address {
    position: absolute; left: 44px; top: 196px;
    font-size: 17px; line-height: 1.4; color: var(--grey); font-style: normal;
  }
  .contact {
    position: absolute; right: 44px; top: 186px;
    text-align: right;
  }
  .person-name {
    font-size: 24px; font-weight: 500; color: var(--orange); letter-spacing: 1.2px;
  }
  .person-title {
    font-size: 17px; color: var(--black); letter-spacing: 0.8px; margin-bottom: 10px;
  }
  .contact-list { list-style: none; font-size: 17px; color: var(--grey); line-height: 1.55; }
  .contact-list li { display: flex; align-items: center; justify-content: flex-end; gap: 10px; }
  .contact-list svg { width: 18px; height: 18px; fill: var(--orange); flex: none; }
</style>
</head>
<body>

  <section class="card card-back">
    <div class="back-band back-band-top"></div>
    <div class="back-mark">
      <div class="mark-dot"></div>
      <span class="mark-name">KVR</span>
    </div>
    <p class="tagline">
      <span class="lead">Industrial Networking &amp; Computing Specialist</span><br>
      Ethernet / Wireless / Cellular<br>
      Routing / Serial / Fieldbus Connectivity<br>
      Industrial &amp; Remote Automation
    </p>
    <div class="back-band back-band-bottom"></div>
  </section>

  <section class="card card-front">
    <div class="brand">
      <div class="brand-dot"></div>
      <span class="brand-name">KVR</span>
    </div>
    <div class="divider"></div>

    <address class="address">
      18 Harbour Link<br>
      Innovation Hub #05-21 (Lobby A)<br>
      Singapore 418732<br>
      www.kvrnet.com.sg
    </address>

    <div class="contact">
      <div class="person-name">DANIEL KOH</div>
      <div class="person-title">SALES MANAGER</div>
      <ul class="contact-list">
        <li>+65 6123 4560
          <svg viewBox="0 0 24 24" aria-hidden="true"><path d="M6.6 10.8a15 15 0 0 0 6.6 6.6l2.2-2.2a1 1 0 0 1 1-.25 11.4 11.4 0 0 0 3.6.6 1 1 0 0 1 1 1V20a1 1 0 0 1-1 1A17 17 0 0 1 3 4a1 1 0 0 1 1-1h3.5a1 1 0 0 1 1 1c0 1.25.2 2.450.6 3.6a1 1 0 0 1-.25 1z"/></svg>
        </li>
        <li>+65 9123 4567
          <svg viewBox="0 0 24 24" aria-hidden="true"><path d="M7 1h10a2 2 0 0 1 2 2v18a2 2 0 0 1-2 2H7a2 2 0 0 1-2-2V3a2 2 0 0 1 2-2zm0 3v14h10V4zm5 15.5a1.2 1.2 0 1 0 0 2.4 1.2 1.2 0 0 0 0-2.4z"/></svg>
        </li>
        <li>+65 6123 4561
          <svg viewBox="0 0 24 24" aria-hidden="true"><path d="M6 2h10l3 3v4h1a2 2 0 0 1 2 2v9a2 2 0 0 1-2 2H4a2 2 0 0 1-2-2v-9a2 2 0 0 1 2-2h2zm2 2v5h9V6h-2V4zm-1 9v2h2v-2zm4 0v2h2v-2zm4 0v2h2v-2z"/></svg>
        </li>
        <li>sales@kvrnet.com.sg
          <svg viewBox="0 0 24 24" aria-hidden="true"><path d="M3 5h18a1 1 0 0 1 1 1v12a1 1 0 0 1-1 1H3a1 1 0 0 1-1-1V6a1 1 0 0 1 1-1zm1 2.2V17h16V7.2l-8 5.3z"/></svg>
        </li>
      </ul>
    </div>
  </section>

</body>
</html>
```